Website Design Request - Management Consulting Firm

We need a Website designed for an IT Management Staffing and Recruiting firm called TRAVENOK based in San Francisco.

The firm is an high-end technology staffing agency. Our focus is on quality and high-caliber candidates rather than quantity.

The website will have two main home pages. One for the recruiter and another on for the candidates.

The website needs to optimize for mobile devices as well.

I have attached few mock-ups that I have done just to show what I am thinking. The UI needs to be very clean, fluid, and it needs to have a modern, rustic, professional feel to it.

Target Market(s)

Technology Manager, Director, VP, CIO of Companies that have $4b-10b dollar revenue. Such as larkspurdwellings.example , https://www.velmorian.example/, quillnet.example, zib.example

Industry/Entity Type

Management Consulting

Number of Pages Required

5+ page

Font styles to use
Sans Serif

Colors
f37122
ffffff

Requirements
Must have
• Please review mock-ups for suggestions
Nice to have
Should not have

```html
<!DOCTYPE html>
<html lang="en">
<head>
<meta charset="utf-8">
<title>TRAVENOK – IT Project Management Jobs</title>
<link href="https://fonts.googleapis.com/css2?family=Cinzel:wght@400;600&family=Open+Sans:wght@400;600&display=swap" rel="stylesheet">
<style>
:root{
  --orange:#f37122;
  --white:#ffffff;
  --ink:#333333;
  --muted:#666666;
  --dark:#2b2b2b;
  --line:#9a9a9a;
  --serif:'Cinzel', serif;
  --sans:'Open Sans', sans-serif;
}
*{margin:0;padding:0;box-sizing:border-box}
html,body{width:921px;height:1200px;overflow:hidden;background:var(--white)}
body{position:relative;font-family:var(--sans);color:var(--ink)}
.abs{position:absolute}
a{color:inherit;text-decoration:none}

.site-header{position:absolute;left:0;top:0;width:921px;height:70px;border-top:3px solid var(--orange);background:var(--white)}
.brand{position:absolute;left:76px;top:8px}
.brand-name{font-family:var(--serif);font-weight:600;color:var(--orange);font-size:34px;line-height:36px;letter-spacing:1px}
.brand-tag{font-family:var(--serif);font-size:8px;letter-spacing:.4px;color:var(--ink);margin-top:1px}
.main-nav a{position:absolute;top:24px;font-size:12.5px;font-weight:600;color:var(--ink)}
.btn-sign{position:absolute;top:19px;height:28px;border-radius:2px;font-size:10.5px;font-weight:600;display:flex;align-items:center;justify-content:center;gap:5px;letter-spacing:.3px}
.btn-in{left:687px;width:72px;border:1px solid #999;color:var(--orange)}
.btn-up{left:773px;width:72px;background:var(--orange);color:var(--white)}

.hero{position:absolute;left:0;top:70px;width:921px;height:360px;background:linear-gradient(100deg,#3f3f3d 0%,#5a5652 35%,#6e6963 60%,#4a4744 100%)}
.hero-title{position:absolute;left:0;width:921px;top:85px;text-align:center;font-family:var(--serif);font-size:30px;color:var(--white);letter-spacing:.5px;text-shadow:0 1px 3px rgba(0,0,0,.5)}
.hero-sub{position:absolute;left:0;width:921px;top:124px;text-align:center;font-size:16.5px;color:var(--white);text-shadow:0 1px 3px rgba(0,0,0,.5)}
.signup-box{position:absolute;left:174px;top:162px;width:573px;height:98px;background:rgba(40,38,36,.82)}
.email-field{position:absolute;left:18px;top:17px;width:401px;height:34px;background:var(--white);font-size:12px;color:#777;padding:9px 14px}
.offers-btn{position:absolute;left:448px;top:17px;width:106px;height:34px;background:var(--orange);color:var(--white);font-size:12px;font-weight:600;display:flex;align-items:center;justify-content:center}
.talent-line{position:absolute;left:0;width:573px;top:68px;text-align:center;font-size:12px;color:var(--white);font-weight:600}
.talent-line a{color:var(--orange);text-decoration:underline;font-weight:400}
.slider-dots{position:absolute;top:321px;left:411px;display:flex;gap:5px}
.slider-dots span{width:22px;height:3px;background:var(--white);border-radius:2px}
.slider-dots span.on{background:var(--orange)}

.tab-band{position:absolute;left:0;top:430px;width:921px;height:41px}
.tab-how{position:absolute;left:0;top:0;width:460px;height:41px;background:var(--orange)}
.tab-why{position:absolute;left:460px;top:0;width:461px;height:41px;background:var(--dark)}
.tab-label{position:absolute;top:9px;font-family:var(--serif);font-size:21px;color:var(--white);width:300px;text-align:center}
.tab-badge{position:absolute;left:431px;top:-7px;width:58px;height:58px;border-radius:50%;background:var(--white)}
.tab-badge i{position:absolute;left:17px;top:17px;width:24px;height:24px;border-radius:50%;background:var(--orange)}

.steps-title{position:absolute;top:511px;width:921px;text-align:center;font-size:19px;color:var(--ink)}
.steps-sub{position:absolute;top:548px;width:921px;text-align:center;font-size:11.5px;color:var(--muted)}
.step{position:absolute;top:593px;width:240px;text-align:center}
.step-circle{position:relative;margin:0 auto;width:163px;height:163px;border:1px solid var(--line);border-radius:50%}
.step-num{position:absolute;right:3px;top:18px;width:27px;height:27px;border-radius:50%;background:#6b6b6b;color:var(--white);font-family:var(--serif);font-size:14px;display:flex;align-items:center;justify-content:center}
.step-circle svg{position:absolute;left:50%;top:50%;transform:translate(-50%,-50%)}
.step-name{margin-top:25px;font-family:var(--serif);font-size:15px;color:var(--ink)}
.step-text{margin-top:6px;font-size:10px;line-height:17px;color:var(--muted)}
.step-arrow{position:absolute;top:648px}

.upload-btn{position:absolute;left:351px;top:873px;width:219px;height:37px;border:1px solid #888;border-radius:2px;color:var(--orange);font-size:12px;font-weight:600;display:flex;align-items:center;justify-content:center;gap:7px}

.site-footer{position:absolute;left:0;top:956px;width:921px;height:244px;border-top:2px solid var(--orange)}
.foot-brand{position:absolute;left:76px;top:76px}
.foot-brand .brand-name{font-size:36px}
.foot-brand .brand-tag{font-size:8.5px}
.foot-col{position:absolute;top:36px}
.foot-col h4{font-family:var(--serif);font-weight:400;font-size:14px;color:var(--ink);margin-bottom:9px}
.foot-col li{list-style:none;font-size:9.5px;color:#555;line-height:18px}
.contact-row{display:flex;gap:10px;font-size:9.5px;color:#555;line-height:13px;margin-bottom:14px}
.contact-row svg{flex:none;margin-top:1px}
.foot-rule{position:absolute;left:76px;top:190px;width:769px;height:1px;background:#d6d6d6}
.copyright{position:absolute;left:76px;top:210px;font-size:9.5px;color:#555}
.social{position:absolute;top:204px;display:flex;gap:6px;left:737px}
.social span{width:23px;height:23px;border:1px solid #999;border-radius:50%;display:flex;align-items:center;justify-content:center}
.social span i{width:6px;height:6px;border-radius:50%;background:var(--orange)}
</style>
</head>
<body>

<header class="site-header">
  <div class="brand"><div class="brand-name">TRAVENOK</div><div class="brand-tag">PROJECT MANAGEMENT CONSULTING</div></div>
  <nav class="main-nav"><a style="left:494px">Professional</a><a style="left:596px">Employers</a></nav>
  <a class="btn-sign btn-in"><svg width="8" height="9" viewBox="0 0 8 9"><rect x="0" y="4" width="8" height="5" fill="#f37122"/><path d="M2 4V2.5a2 2 0 0 1 4 0V4" stroke="#f37122" fill="none" stroke-width="1.2"/></svg>SIGN IN</a>
  <a class="btn-sign btn-up"><svg width="10" height="10" viewBox="0 0 10 10"><rect x=".5" y="1.5" width="7" height="7.5" fill="none" stroke="#fff"/><path d="M4 6l5-5" stroke="#fff" stroke-width="1.4"/></svg>SIGN UP</a>
</header>

<section class="hero" role="img" aria-label="Photo of a person typing on a laptop showing the site">
  <h1 class="hero-title">Looking for IT Project Managemant Jobs?</h1>
  <p class="hero-sub">Upload your Resume, accept interview requests, get offers</p>
  <div class="signup-box">
    <div class="email-field">Email Address</div>
    <div class="offers-btn">GET OFFERS NOW</div>
    <p class="talent-line">Looking for Talents? &nbsp;<a>See how it works for Employers</a></p>
  </div>
  <div class="slider-dots"><span class="on"></span><span></span><span></span><span></span></div>
</section>

<div class="tab-band">
  <div class="tab-how"><div class="tab-label" style="left:87px">How It Works</div></div>
  <div class="tab-why"><div class="tab-label" style="left:74px">Why Us?</div></div>
  <div class="tab-badge"><i></i></div>
</div>

<h2 class="steps-title">Three Simple Steps</h2>
<p class="steps-sub">Employers pay 25% more for a better FIT Project Manager</p>

<div class="step" style="left:60px">
  <div class="step-circle"><span class="step-num">1</span>
    <svg width="62" height="64" viewBox="0 0 62 64" fill="none" stroke="#f37122" stroke-width="3.5"><path d="M33 60H3V2h26l12 12v18"/><path d="M29 2v12h12"/><path d="M10 22h18M10 30h22M10 38h12M10 46h10M10 54h10"/><circle cx="45" cy="46" r="14"/><path d="M45 54V40M39 46l6-6 6 6"/></svg>
  </div>
  <div class="step-name">Upload Your Resume</div>
  <div class="step-text">Answer few questins and upload your resume</div>
</div>
<svg class="step-arrow" style="left:292px" width="58" height="46" viewBox="0 0 58 46" fill="none" stroke="#f37122" stroke-width="1.5"><path d="M4 4c6 20 22 32 50 34"/><path d="M40 28l14 10-14 6"/></svg>

<div class="step" style="left:340px">
  <div class="step-circle"><span class="step-num">2</span>
    <svg width="68" height="68" viewBox="0 0 68 68"><path d="M0 26L34 0l34 26v42H0z" fill="#f37122"/><rect x="12" y="8" width="44" height="36" fill="#fff"/><text x="34" y="36" text-anchor="middle" font-family="Open Sans, sans-serif" font-size="28" font-weight="600" fill="#f37122">@</text><path d="M0 26l34 26 34-26v42H0z" fill="#f37122"/><path d="M2 66l26-22M66 66L40 44" stroke="#fff" stroke-width="2.5"/></svg>
  </div>
  <div class="step-name">We send you interview requests</div>
  <div class="step-text">Interested in someone? With a single click, send<br>interview request and let us handle the best</div>
</div>
<svg class="step-arrow" style="left:570px" width="58" height="46" viewBox="0 0 58 46" fill="none" stroke="#f37122" stroke-width="1.5"><path d="M4 44c4-20 20-34 50-36"/><path d="M40 2l14 6-12 10"/></svg>

<div class="step" style="left:619px">
  <div class="step-circle"><span class="step-num">3</span>
    <svg width="74" height="72" viewBox="0 0 74 72"><g stroke="#f37122" stroke-width="4" fill="none"><circle cx="36" cy="12" r="8"/><circle cx="58" cy="34" r="8"/><path d="M60 4L34 42"/></g><rect x="0" y="42" width="10" height="26" fill="#f37122"/><path d="M13 44h16c6 0 10 4 16 4h8c3 0 3 6 0 6H35v2h20l14-6c5-1 6 4 2 6l-22 12c-6 2-22-2-36-2z" fill="#f37122"/></svg>
  </div>
  <div class="step-name">Get $1000 Bonus</div>
  <div class="step-text">Find a job and get $1000 bonus TRAVENOK</div>
</div>

<a class="upload-btn"><svg width="13" height="12" viewBox="0 0 13 12" fill="#f37122"><path d="M6.5 0L12 5H8.5v4h-4V5H1z"/><rect x="0" y="9.5" width="13" height="2.5"/></svg>UPLOAD YOUR RESUME</a>

<footer class="site-footer">
  <div class="foot-brand"><div class="brand-name">TRAVENOK</div><div class="brand-tag">PROJECT MANAGEMENT CONSULTING</div></div>
  <div class="foot-col" style="left:303px"><h4>About Us</h4><ul><li>Our Story</li><li>Team</li><li>Newsletters</li><li>Contact</li><li>Jobs</li><li>Help Us Grow</li></ul></div>
  <div class="foot-col" style="left:421px"><h4>Quick Links</h4><ul><li>Crewline Projects</li><li>Crewline Desk</li><li>Crewline Chat</li></ul></div>
  <div class="foot-col" style="left:565px"><h4>Resources</h4><ul><li>Careers</li><li>Press</li><li>Privacy Policy</li><li>Terms of Use</li><li>&nbsp;Site Map</li></ul></div>
  <div class="foot-col" style="left:695px"><h4>Contact Us</h4>
    <div class="contact-row"><svg width="9" height="12" viewBox="0 0 9 12"><path d="M4.5 0A4.5 4.5 0 0 0 0 4.5C0 8 4.5 12 4.5 12S9 8 9 4.5A4.5 4.5 0 0 0 4.5 0z" fill="#f37122"/><circle cx="4.5" cy="4.5" r="1.6" fill="#fff"/></svg><span>418 Harlow Street, San Francisco,<br>CA 94107</span></div>
    <div class="contact-row" style="margin-top:4px"><svg width="11" height="11" viewBox="0 0 11 11"><path d="M2 0l2 3-1.2 1.3a7 7 0 0 0 4 4L8 7l3 2-1.5 2C5 11 0 6 0 1.5z" fill="#f37122"/></svg><span>555 014 2290</span></div>
    <div class="contact-row" style="margin-top:6px"><svg width="12" height="9" viewBox="0 0 12 9"><rect width="12" height="9" fill="#f37122"/><path d="M0 0l6 5 6-5" stroke="#fff" fill="none"/></svg><span style="text-decoration:underline">office@travenoktech.example</span></div>
  </div>
  <div class="foot-rule"></div>
  <p class="copyright">Copyrights © 2016, Travenok. All rights reserved.</p>
  <div class="social"><span><i></i></span><span><i></i></span><span><i></i></span><span><i></i></span></div>
</footer>

</body>
</html>
```